Yoga Magazine needs simple business card!

We are a new yoga magazine and need a simple business card!

I also encourage you to design a text logo and maybe even incorporate some form of the "flower" pattern in the solveralogo.jpg and solverayellow.jpg files attached below. I prefer to have the "solvera" word in larger font and then "San Diego" in smaller font somewhere. See the brickhollow.jpg file or also the tarnwillet.jpg file. Our tag line will be something similar to these. If you could incorporate HEALTH, WELLNESS and YOGA LIFESTYLE into the name somehow that'd be really cool. Maybe even add in FITNESS if there is room. Also, please incorporate MAGAZINE somewhere as I want people to know what we are without having to guess.

we are SOLVERA, San Diego's original magazine for Health, Wellness and the Yoga Lifestyle.

Above all, the business card needs to be classy, clean and sophisticated. I want it to look professional.

I have included a few logos that I like. My favorite colors are the chief.jpg and the kamloops.jpg cards, but that doesn't mean that you have to use orange. I'm just looking for something that stands out.

Target Market(s)

Colors are up to you, but I'm leaning toward something soft and subtle, not bold and obnoxious. Font should be soothing and calm. Include pictures in the brochure of pretty people doing yoga, healthy looking food, families with young children. The target audience is women in their late 20s thru 50s and beyond. We will have some male readers, but maybe on 1/4 of readers will be men...so let's lean toward more feminine than masculine.

Industry/Entity Type

Business

Contact Information for Business Card

Ned Parlow
Editor-In-Chief
Solvera San Diego Magazine
847 Quillon Avenue #310
San Diego, CA 92101
www.brelvaport.com
ned@quorvix.com

Font styles to use
Serif

Requirements
Must have
• mellow, calm colors
• accent mark (') above the "e" in solvera.
Nice to have
• small logos in front of contact information that denote location, globe and phone.
• maybe just flower logo and text name on back? let's be creative here. i'll leave up to you all.
• green? yellow? orange? you pick!
• how about black and green? or green and black? :-)
Should not have
• no pictures or cartoon drawings of people doing yoga poses.
• no photography of people doing yoga poses.

```html
<!DOCTYPE html>
<html lang="en">
<head>
<meta charset="utf-8">
<title>Solvera San Diego – Business Card</title>
<link href="https://fonts.googleapis.com/css2?family=Josefin+Sans:wght@400&family=Open+Sans:wght@400;700&display=swap" rel="stylesheet">
<style>
  :root{
    --backdrop-dark:#1b1b1b;
    --backdrop-mid:#3a3a3a;
    --leaf-green:#8cc63f;
    --sun-orange:#f7941d;
    --ink-grey:#555555;
    --card-white:#ffffff;
    --card-mist:#e6e7e9;
    --green-deep:#00a651;
    --green-mid:#4caf47;
    --green-light:#8cc63f;
  }
  *{margin:0;padding:0;box-sizing:border-box}
  html,body{width:1200px;height:999px;overflow:hidden}
  body{position:relative;font-family:"Open Sans",Arial,sans-serif}
  .backdrop{position:absolute;inset:0;background:radial-gradient(ellipse at 50% 55%,var(--backdrop-mid),var(--backdrop-dark) 75%)}
  .brand{position:absolute;left:0;width:1200px;text-align:center;font-family:"Josefin Sans",Arial,sans-serif;font-weight:400;line-height:1}
  .brand-mark{position:absolute;border-radius:50%}
  .hero-mark{left:556px;top:150px;width:88px;height:88px;background:var(--sun-orange)}
  .hero-name{top:300px;font-size:86px;color:var(--leaf-green);letter-spacing:1px}
  .hero-city{top:395px;font-size:40px;color:var(--sun-orange);letter-spacing:2px}

  .card{position:absolute;top:612px;width:552px;height:314px;border-radius:30px;overflow:hidden}
  .card-front{left:19px;background:linear-gradient(to bottom,var(--card-mist),var(--card-white) 30%)}
  .card-back{left:604px}

  .front-mark{left:126px;top:94px;width:44px;height:44px;background:var(--sun-orange)}
  .front-name{position:absolute;left:0;width:272px;top:166px;text-align:center;font-family:"Josefin Sans",Arial,sans-serif;font-size:40px;color:var(--leaf-green);line-height:1}
  .front-city{position:absolute;left:0;width:272px;top:206px;text-align:center;font-family:"Josefin Sans",Arial,sans-serif;font-size:17px;color:var(--sun-orange);letter-spacing:1px;line-height:1}
  .divider{position:absolute;left:270px;top:50px;width:2px;height:214px;background:linear-gradient(to bottom,transparent,var(--ink-grey) 20%,var(--ink-grey) 80%,transparent)}
  .contact{position:absolute;left:306px;top:64px;color:var(--ink-grey);white-space:nowrap}
  .contact-name{font-size:23px;font-weight:700;line-height:30px}
  .contact-title{font-size:13px;line-height:20px;margin-bottom:8px}
  .contact-address{font-size:15px;line-height:19px;margin-bottom:10px}
  .contact-list{list-style:none;font-size:15px;line-height:19px}
  .contact-list li{display:flex;align-items:center;gap:6px}
  .contact-list svg{width:13px;height:13px;fill:var(--ink-grey)}

  .back-field{position:absolute;inset:0;background:linear-gradient(160deg,var(--green-light) 0%,var(--green-mid) 55%,var(--green-deep) 100%)}
  .back-mark{left:253px;top:46px;width:50px;height:50px;border:3px solid var(--card-white)}
  .back-name{position:absolute;left:0;width:552px;top:140px;text-align:center;font-family:"Josefin Sans",Arial,sans-serif;font-size:49px;color:var(--card-white);line-height:1}
  .back-city{position:absolute;left:0;width:552px;top:190px;text-align:center;font-family:"Josefin Sans",Arial,sans-serif;font-size:24px;color:var(--card-white);letter-spacing:1.5px;line-height:1}
  .tagline{position:absolute;left:0;width:552px;top:246px;text-align:center;font-size:14px;color:var(--card-white)}
</style>
</head>
<body>
  <div class="backdrop" role="img" aria-label="Dark quilted diamond-pattern presentation backdrop"></div>

  <div class="brand-mark hero-mark"></div>
  <div class="brand hero-name">SOLVÉRA</div>
  <div class="brand hero-city">SAN DIEGO</div>

  <section class="card card-front">
    <div class="brand-mark front-mark"></div>
    <div class="front-name">SOLVERA</div>
    <div class="front-city">SAN DIEGO</div>
    <div class="divider"></div>
    <div class="contact">
      <div class="contact-name">Ned Parlow</div>
      <div class="contact-title">Editor-In-Chief</div>
      <div class="contact-address">Solvera San Diego Magazine<br>847 Quillon Avenue #310<br>San Diego, CA 92101</div>
      <ul class="contact-list">
        <li><svg viewBox="0 0 13 13"><rect x="0" y="0" width="13" height="13" rx="2"/><rect x="3" y="3" width="7" height="7" fill="#fff"/></svg>000-000-0000</li>
        <li><svg viewBox="0 0 13 13"><rect x="3" y="0" width="7" height="4"/><rect x="0" y="5" width="13" height="5" rx="1"/><rect x="3" y="9" width="7" height="4"/></svg>000-000-0000</li>
        <li><svg viewBox="0 0 13 13"><path d="M0 5 L6.5 1 L13 5 V13 H0 Z"/><path d="M1.5 6 L6.5 9.5 L11.5 6" stroke="#fff" stroke-width="1.2" fill="none"/></svg>ned@quorvix.com</li>
      </ul>
    </div>
  </section>

  <section class="card card-back">
    <div class="back-field" role="img" aria-label="Faceted green geometric background pattern"></div>
    <div class="brand-mark back-mark"></div>
    <div class="back-name">SOLVERA</div>
    <div class="back-city">SAN DIEGO</div>
    <div class="tagline">HEALTH, WELLNESS and YOGA LIFESTYLE</div>
  </section>
</body>
</html>
```